Fenwick yard services house wash and water tank cleaning trailer

Fenwick yard services is an exterior cleaning company, we have built a new trailer for cleaning water tanks and buildings. We would like a design that incorporates our company name, logo, phone number and web page. The trailer has 11 aluminum panels on it as you will see in the pics, we would like a design that brings it all together. The front 2 corner panels get a bit dirty, so our thought were we might be able to have a design that makes the front of the trailer look dirty and the rest look clean. For example a mud splash in the background on the front panels and maybe the front side panels and then the rest of the panels looking like they are soaped up or clean. www.fenwickyardservices.co.nz for details

Requirements
Must have
• A design that is eye catching
Nice to have
• some use of our company colors ( see pics or website ) www.fenwickyardsrevices.co.nz

Website across the rear of the trailer
Should not have
• plain design

```html
<!DOCTYPE html>
<html lang="en">
<head>
<meta charset="utf-8">
<title>Fenwick Yard Services – Trailer Panel Layout</title>
<link rel="stylesheet" href="https://fonts.googleapis.com/css2?family=Stardos+Stencil:wght@700&family=Inconsolata:wght@500&family=Arimo:wght@400;700&display=swap">
<style>
  :root {
    --brand-yellow: #fbef00;
    --ink: #1c1c1c;
    --grass: #5fbf1c;
    --grass-light: #b8e25a;
    --tank-blue: #1f8fd6;
    --mud: #8a5a2c;
    --outline: #9a9a9a;
    --dim-text: #333;
    --paper: #ffffff;
  }
  html, body { margin: 0; padding: 0; width: 1200px; height: 801px; overflow: hidden; background: var(--paper); }
  .panel-layout { display: block; width: 1200px; height: 801px; }
  .stencil { font-family: "Stardos Stencil", "Georgia", serif; font-weight: 700; fill: var(--ink); }
  .web-address { font-family: "Inconsolata", "Courier New", monospace; fill: var(--ink); }
  .sans { font-family: "Arimo", "Arial", sans-serif; fill: var(--ink); }
  .sans-bold { font-family: "Arimo", "Arial", sans-serif; font-weight: 700; fill: var(--ink); }
  .dimension { font-family: "Arimo", "Arial", sans-serif; font-size: 24px; fill: var(--dim-text); }
  .brand-fill { fill: var(--brand-yellow); }
  .ink-fill { fill: var(--ink); }
  .edge-line { stroke: var(--ink); stroke-width: 4; fill: none; }
  .panel-outline { stroke: var(--outline); stroke-width: 3; }
</style>
</head>
<body>
<svg class="panel-layout" viewBox="0 0 2340 1562" xmlns="http://www.w3.org/2000/svg">
  <defs>
    <linearGradient id="grassFade" x1="0" y1="0" x2="0" y2="1">
      <stop offset="0" stop-color="#ffffff" stop-opacity="0"/>
      <stop offset="0.35" stop-color="var(--grass-light)"/>
      <stop offset="1" stop-color="var(--grass)"/>
    </linearGradient>
    <linearGradient id="panelFade" x1="0" y1="0" x2="0" y2="1">
      <stop offset="0" stop-color="var(--brand-yellow)"/>
      <stop offset="0.75" stop-color="#ffffff"/>
      <stop offset="1" stop-color="#ffffff"/>
    </linearGradient>
    <linearGradient id="tankShade" x1="0" y1="0" x2="1" y2="0">
      <stop offset="0" stop-color="#1668b0"/>
      <stop offset="0.5" stop-color="var(--tank-blue)"/>
      <stop offset="1" stop-color="#1668b0"/>
    </linearGradient>
    <radialGradient id="mudSplash" cx="0.6" cy="0.8" r="0.7">
      <stop offset="0" stop-color="var(--mud)"/>
      <stop offset="1" stop-color="var(--mud)" stop-opacity="0"/>
    </radialGradient>
  </defs>

  <!-- Rear panels -->
  <g class="rear-panels">
    <text class="dimension" x="1199" y="80" text-anchor="middle">2325 mm</text>
    <rect class="brand-fill" x="125" y="102" width="316" height="169"/>
    <rect class="brand-fill" x="528" y="102" width="1347" height="169"/>
    <text class="stencil" x="1210" y="195" font-size="68" text-anchor="middle" letter-spacing="2">FENWICK YARD SERVICES</text>
    <text class="web-address" x="1225" y="255" font-size="52" text-anchor="middle">www.fenwickyardservices.co.nz</text>
    <rect class="brand-fill" x="1949" y="102" width="316" height="169"/>
    <circle class="ink-fill" cx="2000" cy="186" r="16"/>
    <text class="sans-bold" x="2026" y="198" font-size="34">@fenwickyard</text>
    <text class="dimension" x="2128" y="296" text-anchor="middle">550 mm</text>
    <text class="dimension" transform="translate(2305 176) rotate(-90)" text-anchor="middle">295 mm</text>
  </g>

  <!-- Upper side panels -->
  <g class="side-panels-upper">
    <text class="dimension" x="620" y="347" text-anchor="middle">1305 mm</text>
    <text class="dimension" transform="translate(380 424) rotate(-90)" text-anchor="middle">270 mm</text>
    <polygon class="brand-fill" points="675,370 1148,370 1060,460 675,460"/>
    <polygon fill="url(#grassFade)" points="398,455 1063,455 985,538 398,538" role="img" aria-label="Band of green grass"/>
    <rect class="ink-fill" x="418" y="388" width="72" height="72"/>
    <path class="edge-line" d="M398 368 H1150 L985 538 H398"/>
    <text class="stencil" x="688" y="428" font-size="56">FENWICK</text>
    <text class="stencil" x="688" y="453" font-size="27">YARD SERVICES</text>
    <text class="dimension" x="628" y="572" text-anchor="middle">1037 mm</text>

    <polygon class="brand-fill" points="1254,374 2005,374 2005,467 1345,467"/>
    <polygon fill="url(#grassFade)" points="1340,462 2005,462 2005,545 1420,545" role="img" aria-label="Band of green grass"/>
    <path class="edge-line" d="M1252 373 H2005 M1252 373 L1420 545 H2005"/>
    <text class="sans-bold" x="1965" y="443" font-size="38" text-anchor="end">Your Exterior Property Specialists</text>
  </g>

  <!-- Lower side panels -->
  <g class="side-panels-lower">
    <text class="dimension" transform="translate(380 667) rotate(-90)" text-anchor="middle">270 mm</text>
    <polygon class="brand-fill" points="650,633 1125,633 1060,700 650,700"/>
    <polygon fill="url(#grassFade)" points="398,695 1065,695 985,778 398,778" role="img" aria-label="Band of green grass"/>
    <rect class="ink-fill" x="428" y="635" width="62" height="62"/>
    <path class="edge-line" d="M398 608 H1150 L985 778 H398"/>
    <text class="stencil" x="662" y="690" font-size="64">FENWICK</text>
    <text class="dimension" x="620" y="823" text-anchor="middle">1305 mm</text>

    <polygon class="brand-fill" points="1265,633 1998,633 1998,700 1330,700"/>
    <polygon fill="url(#grassFade)" points="1325,695 1998,695 1998,785 1413,785" role="img" aria-label="Band of green grass"/>
    <path class="edge-line" d="M1245 614 H1998 M1245 614 L1413 785 H1998"/>
    <text class="stencil" x="1962" y="688" font-size="52" text-anchor="end">YARD SERVICES</text>
  </g>

  <!-- Phone strip -->
  <g class="phone-strip">
    <rect class="brand-fill" x="443" y="872" width="307" height="40"/>
    <rect class="brand-fill" x="1631" y="869" width="308" height="40"/>
    <text class="dimension" x="1222" y="826" text-anchor="middle">1030 mm</text>
    <rect class="brand-fill" x="901" y="845" width="591" height="90"/>
    <circle cx="952" cy="890" r="27" fill="none" stroke="var(--ink)" stroke-width="5"/>
    <path class="ink-fill" d="M941 876 l7 -3 l5 9 l-5 4 q3 7 9 11 l4 -5 l9 5 l-3 7 q-14 2 -26 -28z"/>
    <text class="stencil" x="1000" y="917" font-size="80" letter-spacing="4">21 555 0147</text>
    <text class="dimension" transform="translate(1525 890) rotate(-90)" text-anchor="middle">160 mm</text>
  </g>

  <!-- Water tank panel -->
  <g class="water-tank-panel">
    <text class="dimension" x="300" y="991" text-anchor="middle">682 mm</text>
    <text class="dimension" transform="translate(80 1256) rotate(-90)" text-anchor="middle">880 mm</text>
    <text class="dimension" transform="translate(503 1256) rotate(-90)" text-anchor="middle">850 mm</text>
    <rect class="panel-outline" x="84" y="998" width="394" height="507" fill="url(#panelFade)"/>
    <rect class="brand-fill" x="86" y="1000" width="390" height="78"/>
    <text class="stencil" x="112" y="1042" font-size="29">WATER TANK</text>
    <text class="stencil" x="112" y="1070" font-size="29">CLEANING</text>
    <text class="sans" x="110" y="1107" font-size="19">•&#160;&#160;&#160;Water Tank Clean</text>
    <text class="sans" x="110" y="1140" font-size="19">•&#160;&#160;&#160;Water Tank Clean &amp; Sanitize</text>
    <rect x="86" y="1415" width="390" height="88" fill="url(#grassFade)" role="img" aria-label="Grass along the bottom edge"/>
    <rect x="165" y="1185" width="245" height="295" rx="18" fill="url(#tankShade)" role="img" aria-label="Photo of a blue plastic water tank"/>
  </g>

  <!-- Front corner panels -->
  <g class="front-corner-panels">
    <polygon class="panel-outline" points="652,992 777,1338 779,1480 652,1480" fill="url(#panelFade)"/>
    <polygon points="654,1400 778,1400 779,1478 654,1478" fill="url(#grassFade)" role="img" aria-label="Grass along the bottom edge"/>
    <text class="dimension" transform="translate(643 1258) rotate(-90)" text-anchor="middle">840 mm</text>
    <text class="dimension" transform="translate(737 1160) rotate(70)" text-anchor="middle">580 mm</text>
    <text class="dimension" transform="translate(810 1410) rotate(-90)" text-anchor="middle">260 mm</text>
    <text class="dimension" x="718" y="1510" text-anchor="middle">210 mm</text>

    <polygon class="panel-outline" points="1641,992 1641,1480 1515,1480 1517,1338" fill="url(#panelFade)"/>
    <polygon points="1516,1400 1640,1400 1640,1478 1516,1478" fill="url(#grassFade)" role="img" aria-label="Grass with mud splashes"/>
    <ellipse cx="1600" cy="1440" rx="40" ry="30" fill="url(#mudSplash)"/>
    <text class="dimension" transform="translate(1673 1410) rotate(-90)" text-anchor="middle">260 mm</text>
    <text class="dimension" x="1578" y="1510" text-anchor="middle">210 mm</text>
  </g>

  <!-- Front panel -->
  <g class="front-panel">
    <text class="dimension" x="1146" y="985" text-anchor="middle">770 mm</text>
    <rect x="915" y="991" width="462" height="331" fill="var(--brand-yellow)" stroke="#f3e100" stroke-width="3"/>
    <rect class="ink-fill" x="1101" y="1011" width="88" height="88"/>
    <text class="stencil" x="1142" y="1165" font-size="64" text-anchor="middle">FENWICK</text>
    <rect class="ink-fill" x="916" y="1174" width="461" height="52"/>
    <text class="stencil" x="1146" y="1212" font-size="34" text-anchor="middle" style="fill: var(--brand-yellow)">YARD SERVICES</text>
    <text class="sans" x="1146" y="1253" font-size="25" text-anchor="middle">Your Exterior Property Specialists</text>
    <circle cx="983" cy="1286" r="19" fill="#f08a1c" stroke="var(--ink)" stroke-width="3"/>
    <text class="stencil" x="1015" y="1303" font-size="50" letter-spacing="3">21 555 0147</text>
    <rect class="panel-outline" x="916" y="1328" width="461" height="145" fill="#fff"/>
    <rect x="917" y="1365" width="459" height="107" fill="url(#grassFade)" role="img" aria-label="Grass with a light mud splash"/>
    <ellipse cx="1350" cy="1410" rx="30" ry="36" fill="url(#mudSplash)"/>
    <text class="dimension" transform="translate(1417 1190) rotate(-90)" text-anchor="middle">550 mm</text>
    <text class="dimension" transform="translate(1417 1400) rotate(-90)" text-anchor="middle">285 mm</text>
  </g>

  <!-- Exterior cleaning panel -->
  <g class="exterior-cleaning-panel">
    <text class="dimension" x="2046" y="979" text-anchor="middle">682 mm</text>
    <text class="dimension" transform="translate(1825 1245) rotate(-90)" text-anchor="middle">880 mm</text>
    <text class="dimension" transform="translate(2250 1245) rotate(-90)" text-anchor="middle">850 mm</text>
    <rect class="panel-outline" x="1829" y="985" width="393" height="507" fill="url(#panelFade)"/>
    <rect x="1831" y="1410" width="389" height="80" fill="url(#grassFade)" role="img" aria-label="Grass along the bottom edge"/>
    <ellipse cx="2080" cy="1400" rx="150" ry="110" fill="url(#mudSplash)" role="img" aria-label="Mud splash rising from the ground"/>
    <text class="stencil" x="1857" y="1032" font-size="29">EXTERIOR PROPERTY</text>
    <text class="stencil" x="1857" y="1062" font-size="29">CLEANING</text>
    <g class="sans" font-size="18">
      <text x="1855" y="1095">•&#160;&#160;Water Blasting</text>
      <text x="1855" y="1128">•&#160;&#160;House Washing / Soft wash</text>
      <text x="1855" y="1161">•&#160;&#160;Spouting/ Gutter Clearing</text>
      <text x="1855" y="1194">•&#160;&#160;Deck Cleaning</text>
      <text x="1855" y="1227">•&#160;&#160;Moss and Mould Treatment</text>
      <text x="1855" y="1260">•&#160;&#160;Cleaning Driveways and Paths</text>
      <text x="1855" y="1293">•&#160;&#160;Sanitize Playground Equipment</text>
      <text x="1855" y="1326">•&#160;&#160;Sanitize Outdoor Seating</text>
      <text x="1855" y="1358">•&#160;&#160;Clean Solar Panels</text>
      <text x="1855" y="1391">•&#160;&#160;Fence Cleaning</text>
    </g>
  </g>
</svg>
</body>
</html>
```